Business card design needed

I run a Beautician studio (for 7 years now)
I offer
- Velmo Body Sugaring
- Ruby Glaze
- Nails
- Facials
- Manicure
- Foot Treatment
It might not be necessary to list all those treatments?
Maybe the link to the Website is sufficient?
I leave that up to you ...
(more info on www.FernAndDewByLenka.com.au)
Velmo BodySugaring is our biggest success, It replaces waxing.
I would like to incorporate the logo into the Business Card.
We had many complaints regarding our old Business Cards as the Phone Number was to small.
On the backside, we would like a "your next Appointment" section.
Looking forward to you Design, cheers ... Lenka
Industry/Entity Type
Business
Contact Information for Business Card
Fern by Dew by Lenka
14 Korrin Sqr 3942 Berwick
www.FernAndDewByLenka.com.au
03 9481 2267

```html
<!DOCTYPE html>
<html lang="en">
<head>
<meta charset="utf-8">
<title>Fern by Dew by Lenka – Business &amp; Appointment Cards</title>
<link href="https://fonts.googleapis.com/css2?family=Marcellus&family=Open+Sans:wght@400;600&display=swap" rel="stylesheet">
<style>
  :root {
    --backdrop: #1e1e1e;
    --card: #ffffff;
    --green: #1f9a48;
    --ink: #2b2b2b;
    --grey: #555555;
    --line: #9a9a9a;
    --orange-deep: #e8542a;
    --orange-mid: #f08a24;
    --yellow: #f6c42a;
    --watermark: rgba(190, 190, 190, 0.16);
  }
  * { box-sizing: border-box; margin: 0; padding: 0; }
  html, body { width: 1200px; height: 728px; overflow: hidden; background: var(--backdrop); }
  .sheet { position: relative; width: 1200px; height: 728px; }
  .card {
    position: absolute; width: 526px; height: 300px;
    background: var(--card); overflow: hidden;
    font-family: "Open Sans", Arial, sans-serif; color: var(--grey);
  }
  .card--front { left: 41px; top: 36px; }
  .card--appt-a { left: 597px; top: 36px; }
  .card--hours { left: 41px; top: 368px; }
  .card--appt-b { left: 605px; top: 372px; }

  /* brand name: one font, one weight, one colour, plain dot beside */
  .brand { position: absolute; left: 0; right: 0; display: flex; justify-content: center; align-items: center; gap: 10px; }
  .brand__dot { flex: none; border-radius: 50%; background: var(--orange-mid); }
  .brand__name { font-family: "Open Sans", Arial, sans-serif; font-weight: 600; color: var(--ink); white-space: nowrap; }

  /* front */
  .card--front .brand { top: 92px; }
  .card--front .brand__dot { width: 18px; height: 18px; }
  .card--front .brand__name { font-size: 24px; }
  .business-name { position: absolute; top: 174px; width: 100%; text-align: center;
    font-family: "Marcellus", Georgia, serif; font-weight: 400; font-size: 24px;
    letter-spacing: 2px; color: var(--green); }
  .front-band { position: absolute; left: 0; bottom: 0; width: 526px; height: 98px; }
  .front-address { position: absolute; top: 238px; width: 100%; text-align: center;
    font-family: "Marcellus", Georgia, serif; color: #fff; font-size: 14px; letter-spacing: 2.5px; }
  .front-contact { position: absolute; top: 266px; width: 100%; display: flex;
    justify-content: center; align-items: center; gap: 7px;
    font-family: "Marcellus", Georgia, serif; color: #fff; letter-spacing: 0.5px; }
  .front-contact svg { width: 15px; height: 15px; }
  .front-contact .phone { font-size: 19px; }
  .front-contact .web { font-size: 14px; }
  .front-contact .gap { width: 6px; }

  /* appointment */
  .appt-title { position: absolute; left: 34px; top: 52px; font-family: "Marcellus", Georgia, serif;
    font-weight: 400; color: var(--green); font-size: 19px; }
  .field { position: absolute; left: 34px; font-size: 14px; color: var(--ink); display: flex; align-items: center; }
  .dots { border-bottom: 1px dotted var(--line); height: 1px; margin-top: 6px; }
  .rule { border-bottom: 1px solid var(--line); height: 1px; margin-top: 6px; }
  .box { display: inline-block; border: 1px solid #777; height: 20px; }
  .days { position: absolute; left: 30px; top: 201px; display: flex; align-items: center;
    font-weight: 600; font-size: 14px; color: var(--grey); }
  .days .box { width: 34px; margin: 0 9px 0 8px; }
  .notice { position: absolute; left: 30px; top: 250px; width: 455px; font-size: 12.5px;
    line-height: 1.4; color: var(--ink); }
  .card--appt-a .brand { left: auto; right: 40px; top: 72px; gap: 6px; }
  .card--appt-a .brand__dot { width: 10px; height: 10px; }
  .card--appt-a .brand__name { font-size: 12px; }
  .watermark { position: absolute; left: 120px; top: 108px; width: 400px; text-align: center;
    font-family: "Open Sans", Arial, sans-serif; font-weight: 600; color: var(--watermark);
    font-size: 46px; line-height: 1.15; }

  /* hours */
  .card--hours .brand { top: 68px; }
  .card--hours .brand__dot { width: 22px; height: 22px; }
  .card--hours .brand__name { font-size: 30px; }
  .hours-web { position: absolute; top: 200px; width: 100%; text-align: center;
    font-size: 14px; letter-spacing: 2px; color: var(--ink); }
  .hours-title { position: absolute; top: 232px; width: 100%; text-align: center;
    font-size: 19px; font-weight: 600; letter-spacing: 1.5px; color: var(--grey); }
  .hours-times { position: absolute; top: 268px; width: 100%; text-align: center;
    font-size: 15px; font-weight: 600; color: var(--grey); }
  .hours-times .sep { color: #aaa; margin: 0 8px; font-weight: 400; }
</style>
</head>
<body>
<main class="sheet">

  <section class="card card--front">
    <div class="brand">
      <span class="brand__dot"></span>
      <span class="brand__name">Velmo Body Sugaring</span>
    </div>
    <h1 class="business-name">Fern by Dew by Lenka</h1>
    <svg class="front-band" viewBox="0 0 526 98" preserveAspectRatio="none" aria-hidden="true">
      <defs>
        <linearGradient id="bandFill" x1="0" x2="1" y1="0" y2="0">
          <stop offset="0" stop-color="#e8542a"/>
          <stop offset="0.55" stop-color="#f08a24"/>
          <stop offset="1" stop-color="#f6c42a"/>
        </linearGradient>
      </defs>
      <path d="M0 48 Q263 -6 526 38 L526 98 L0 98 Z" fill="url(#bandFill)"/>
      <path d="M0 40 Q263 -16 526 32" fill="none" stroke="#1f9a48" stroke-width="4"/>
    </svg>
    <p class="front-address">14 Korrin Sqr 3942 Berwick</p>
    <p class="front-contact">
      <svg viewBox="0 0 16 16" aria-hidden="true"><circle cx="8" cy="8" r="7" fill="none" stroke="#fff" stroke-width="1.4"/><path d="M5 4.5l1.6-.4 1 2-1 .9c.5 1 1.3 1.8 2.3 2.3l.9-1 2 1-.4 1.6c-3.3.2-6.6-3.1-6.4-6.4z" fill="#fff"/></svg>
      <span class="phone">03 9481 2267</span><span class="gap"></span>
      <svg viewBox="0 0 16 16" aria-hidden="true"><circle cx="8" cy="8" r="7" fill="none" stroke="#fff" stroke-width="1.4"/><ellipse cx="8" cy="8" rx="3" ry="7" fill="none" stroke="#fff" stroke-width="1.2"/><path d="M1 8h14" stroke="#fff" stroke-width="1.2"/></svg>
      <span class="web">www.FernAndDewByLenka.com.au</span>
    </p>
  </section>

  <section class="card card--appt-a">
    <div class="brand">
      <span class="brand__dot"></span>
      <span class="brand__name">Velmo Body Sugaring</span>
    </div>
    <h2 class="appt-title">YOUR APPOINTMENT</h2>
    <div class="field" style="top:88px">Name :<span class="dots" style="width:290px;margin-left:10px"></span></div>
    <div class="field" style="top:126px">Date :<span class="rule" style="width:96px;margin-left:20px"></span>&nbsp;Time :<span class="rule" style="width:90px;margin-left:6px"></span>am / pm</div>
    <div class="field" style="top:163px">Next Appointment<span class="box" style="width:96px;margin-left:10px"></span><span class="box" style="width:96px;margin-left:30px"></span></div>
    <div class="days">MON<span class="box"></span>TUE<span class="box"></span>WED<span class="box"></span>THU<span class="box"></span>FRI<span class="box"></span>SAT<span class="box"></span></div>
    <p class="notice">It would be appreciated if 24 hours notice could be given if you are unable to attend an appointment</p>
  </section>

  <section class="card card--hours">
    <div class="brand">
      <span class="brand__dot"></span>
      <span class="brand__name">Velmo Body Sugaring</span>
    </div>
    <p class="hours-web">www.FernAndDewByLenka.com.au</p>
    <h2 class="hours-title">Hours of Operation</h2>
    <p class="hours-times">Mon - Fri: 7.30am - 7.00pm<span class="sep">|</span>Saturday: 7.30am - 12.00pm</p>
  </section>

  <section class="card card--appt-b">
    <div class="watermark" aria-hidden="true">Velmo<br>Body Sugaring</div>
    <h2 class="appt-title">YOUR APPOINTMENT</h2>
    <div class="field" style="top:88px">Name :<span class="dots" style="width:290px;margin-left:10px"></span></div>
    <div class="field" style="top:126px">Date :<span class="rule" style="width:96px;margin-left:20px"></span>&nbsp;Time :<span class="rule" style="width:90px;margin-left:6px"></span>am / pm</div>
    <div class="field" style="top:163px">Next Appointment<span class="box" style="width:96px;margin-left:10px"></span><span class="box" style="width:96px;margin-left:30px"></span></div>
    <div class="days">MON<span class="box"></span>TUE<span class="box"></span>WED<span class="box"></span>THU<span class="box"></span>FRI<span class="box"></span>SAT<span class="box"></span></div>
    <p class="notice">It would be appreciated if 24 hours notice could be given if you are unable to attend an appointment</p>
  </section>

</main>
</body>
</html>
```